New Business Card Design for Manufacturing

We are an engineering/manufacturing company that offers Advanced machining/assembly/engineering services, as well as innovative products for the heavy duty engine cooling markets.

We are looking to get a new business card designed that is clean and modern looking, but still fits the wide range of technical/skilled work we do.

- We hope to use this design as the base for other design work in new Presentations, web, and print work.

Industry/Entity Type

Engineering

Contact Information for Business Card

Our preferred color of blue is (RGB) 22/71/159 but can vary slightly from that color. Our content will be our Logo and full company name (Vantrell Forge Works, Inc.), company address, name, job title, phone number with extension, cell number, fax number, website, and email address on the cards.
We'd like the full company name next to the logo, but we are open to other interpretations of that layout.
Preferably, we would like the back side to be clean with just our logo, and the front to contain all of the contact information.

Colors
2f74b4
0355a3
85abd2

Requirements
Must have
• - Logo, company name, needed content - We are open to interpretation beyond that.
• - Standard size business card.
• - Horizontal orientation.
• - Enough space for lengthy names / job titles (for example, a job title could read "Directory of Human Resources" or "V.P. of Governmental Affairs"). We need this to look clean, whether the title be short (CEO) or long (as described above).

```html
<!DOCTYPE html>
<html lang="en">
<head>
<meta charset="utf-8">
<title>Vantrell Forge Works – Business Card</title>
<link rel="stylesheet" href="https://fonts.googleapis.com/css2?family=Open+Sans:wght@400;600;800&display=swap">
<style>
  :root {
    --brand-blue: #0d53a0;
    --sky-blue: #1a8fce;
    --mid-blue: #8fb6df;
    --pale-blue: #cfdff1;
    --accent-cyan: #4fb6e6;
    --ink: #3a3a3a;
    --ink-soft: #555;
    --paper: #ffffff;
    --backdrop: #e6e8eb;
  }
  * { box-sizing: border-box; margin: 0; padding: 0; }
  html, body { width: 1200px; height: 1000px; overflow: hidden; }
  body {
    background: var(--backdrop);
    font-family: "Open Sans", Arial, sans-serif;
    position: relative;
  }
  .card {
    position: absolute;
    width: 700px;
    height: 400px;
    background: var(--paper);
    overflow: hidden;
    box-shadow: 0 10px 30px rgba(0,0,0,.18);
  }
  .card-front { left: 70px; top: 60px; }
  .card-back { left: 430px; top: 540px; }
  .card-shapes { position: absolute; inset: 0; }

  /* front */
  .company-tab {
    position: absolute; left: 26px; top: 63px;
    color: var(--paper); font-weight: 800; font-size: 15px;
    line-height: 15px; text-transform: uppercase; letter-spacing: .2px;
  }
  .company-tab small { font-size: 7px; }
  .brand-mark {
    position: absolute; display: flex; align-items: center; gap: 6px;
    color: var(--brand-blue); font-weight: 800; white-space: nowrap;
  }
  .brand-mark .dot { background: var(--brand-blue); display: block; }
  .front-mark { right: 34px; top: 24px; font-size: 18px; }
  .front-mark .dot { width: 10px; height: 10px; }
  .person-name {
    position: absolute; left: 40px; top: 128px;
    font-size: 23px; font-weight: 400; color: var(--ink); letter-spacing: 1px;
  }
  .person-title {
    position: absolute; left: 42px; top: 162px;
    font-size: 12.5px; color: var(--ink-soft); letter-spacing: 1px;
  }
  .contact {
    position: absolute; list-style: none;
    color: var(--paper); font-size: 13px; letter-spacing: 1px; white-space: nowrap;
  }
  .contact li { display: flex; align-items: center; gap: 10px; height: 25px; }
  .contact svg { width: 14px; height: 14px; fill: currentColor; flex: none; }
  .contact-address { left: 200px; top: 196px; color: var(--ink-soft); }
  .contact-web { left: 520px; top: 208px; }
  .contact-phone { left: 46px; top: 275px; }

  /* back */
  .back-mark { left: 50%; top: 205px; transform: translateX(-50%); font-size: 40px; }
  .back-mark .dot { width: 20px; height: 20px; }
  .back-url {
    position: absolute; left: 230px; right: 40px; top: 318px; text-align: center;
    color: var(--paper); font-size: 18px; letter-spacing: .5px;
  }
</style>
</head>
<body>

<section class="card card-front" aria-label="Business card front">
  <svg class="card-shapes" viewBox="0 0 700 400" aria-hidden="true">
    <path d="M0 240 H400 C450 240 465 192 510 188 H700 V400 H0 Z" fill="var(--brand-blue)"/>
    <path d="M250 55 H350 C360 55 360 115 320 115 H250 Z" fill="var(--pale-blue)"/>
    <path d="M190 55 H280 C290 55 290 115 250 115 H190 Z" fill="var(--mid-blue)"/>
    <path d="M0 55 H215 C225 55 225 115 185 115 H0 Z" fill="var(--sky-blue)"/>
  </svg>
  <div class="company-tab">Vantrell<br>Forge<br>Works <small>INC</small></div>
  <div class="brand-mark front-mark"><span class="dot"></span>Vantrell Forge</div>
  <h1 class="person-name">NAME OF CEO</h1>
  <p class="person-title">DIRECTORY OF HUMAN RESOURCES</p>
  <ul class="contact contact-address">
    <li><svg viewBox="0 0 24 24"><path d="M12 2a7 7 0 0 0-7 7c0 5 7 13 7 13s7-8 7-13a7 7 0 0 0-7-7zm0 9.5A2.5 2.5 0 1 1 12 6.5a2.5 2.5 0 0 1 0 5z"/></svg>YOUR COMPANY ADDRESS</li>
  </ul>
  <ul class="contact contact-web">
    <li><svg viewBox="0 0 24 24"><path d="M12 2a10 10 0 1 0 0 20 10 10 0 0 0 0-20zm6.9 6h-3a15 15 0 0 0-1.3-3.9A8 8 0 0 1 18.9 8zM12 4c.8 1.2 1.5 2.5 1.900 4h-3.8c.4-1.5 1.1-2.8 1.9-4zM4.3 14a8 8 0 0 1 0-4h3.4a16 16 0 0 0 0 4zm.8 2h3a15 15 0 0 0 1.3 3.9A8 8 0 0 1 5.1 16zm3-8h-3a8 8 0 0 1 4.3-3.9A15 15 0 0 0 8.1 8zM12 20c-.8-1.2-1.5-2.5-1.9-4h3.8c-.4 1.5-1.1 2.8-1.9 4zm2.3-6H9.7a14 14 0 0 1 0-4h4.6a14 14 0 0 1 0 4zm.3 5.9a15 15 0 0 0 1.3-3.9h3a8 8 0 0 1-4.3 3.9zm1.7-5.9a16 16 0 0 0 0-4h3.4a8 8 0 0 1 0 4z"/></svg>WEBSITE</li>
    <li><svg viewBox="0 0 24 24"><path d="M2 5h20v14H2zm2 2v.5l8 5 8-5V7z"/></svg>EMAIL ADDRESS</li>
  </ul>
  <ul class="contact contact-phone">
    <li><svg viewBox="0 0 24 24"><path d="M3 7c0-2 4-4 9-4s9 2 9 4v2h-5V7H8v2H3zm3 4h12l2 9H4zm6 2a3 3 0 1 0 0 6 3 3 0 0 0 0-6z"/></svg>PHONE NUMBER</li>
    <li><svg viewBox="0 0 24 24"><path d="M6.6 10.8a15 15 0 0 0 6.6 6.6l2.2-2.2c.3-.3.7-.4 1-.2 1.1.4 2.3.6 3.6.6.6 0 1 .4 1 1V20c0 .6-.4 1-1 1A17 17 0 0 1 3 4c0-.6.4-1 1-1h3.5c.6 0 1 .4 1 1 0 1.3.2 2.5.6 3.6.1.3 0 .7-.2 1z"/></svg>CELL NUMBER</li>
    <li><svg viewBox="0 0 24 24"><path d="M7 3h10v5H7zM3 9h18v9h-4v3H7v-3H3zm6 7v3h6v-3z"/></svg>FAX NUMBER</li>
  </ul>
</section>

<section class="card card-back" aria-label="Business card back">
  <svg class="card-shapes" viewBox="0 0 700 400" aria-hidden="true">
    <path d="M0 0 H700 V60 C700 110 680 130 640 140 L170 150 C90 152 40 170 0 200 Z" fill="var(--brand-blue)"/>
    <line x1="0" y1="300" x2="700" y2="300" stroke="var(--accent-cyan)" stroke-width="3"/>
    <path d="M230 300 H660 V325 C660 350 645 362 615 362 H270 C250 362 240 350 230 340 Z" fill="var(--accent-cyan)"/>
  </svg>
  <div class="brand-mark back-mark"><span class="dot"></span>Vantrell Forge</div>
  <p class="back-url">www.website.com</p>
</section>

</body>
</html>
```